Dental specialist needs a sharp looking letterhead

I am looking for a letterhead to be used to send letters and communication between myself (a dental specialist) and other dentists.
My office is a state of the art dental specialty office.
I need to letterhead to also state:
Bertram L. Oswick DDS
2748 Tollard Avenue, Suite K
West Tollard, NY 14391
(716)392-5061
fax: (716)392-5087
oswickroot.com (**this email address may change)

i included my logo designs.
thank you

Target Market(s)

dentists

Industry/Entity Type

Communication

Requirements
Must have
• the included logo, whether the vertical or horizontal versions

```html
<!DOCTYPE html>
<html lang="en">
<head>
<meta charset="utf-8">
<title>Keystone Endodontics P.C. Letterhead</title>
<link href="https://fonts.googleapis.com/css2?family=Roboto+Slab:wght@600&family=PT+Sans:wght@400&display=swap" rel="stylesheet">
<style>
  :root {
    --paper: #ffffff;
    --ink: #1a1a1a;
    --brand-blue: #3fa6dd;
    --divider: #cfd4d8;
  }
  html, body {
    margin: 0;
    padding: 0;
    width: 931px;
    height: 1200px;
    overflow: hidden;
    background: var(--paper);
  }
  .letterhead {
    position: relative;
    width: 931px;
    height: 1200px;
    background: var(--paper);
    color: var(--ink);
  }
  .brand {
    position: absolute;
    top: 28px;
    left: 0;
    width: 100%;
    height: 110px;
  }
  .brand-dot {
    position: absolute;
    left: 318px;
    top: 40px;
    width: 46px;
    height: 46px;
    border-radius: 50%;
    background: var(--brand-blue);
  }
  .brand-rule {
    position: absolute;
    left: 386px;
    top: 0;
    width: 1px;
    height: 100px;
    background: #555;
  }
  .brand-name {
    position: absolute;
    left: 400px;
    top: 46px;
    margin: 0;
    font-family: "Roboto Slab", Georgia, serif;
    font-weight: 600;
    font-size: 24px;
    letter-spacing: 0.2px;
    color: var(--ink);
    white-space: nowrap;
  }
  .practitioner {
    position: absolute;
    left: 408px;
    top: 82px;
    margin: 0;
    font-family: "Roboto Slab", Georgia, serif;
    font-weight: 600;
    font-size: 15px;
    color: var(--ink);
    white-space: nowrap;
  }
  .footer {
    position: absolute;
    left: 0;
    top: 1106px;
    width: 100%;
    font-family: "PT Sans", Arial, sans-serif;
    text-align: center;
  }
  .address {
    margin: 0;
    font-size: 16px;
    line-height: 24px;
  }
  .footer-rule {
    display: block;
    margin: 8px auto 6px;
  }
  .contacts {
    margin: 0;
    font-size: 16px;
    line-height: 24px;
  }
  .contacts .sep {
    display: inline-block;
    width: 1px;
    height: 16px;
    background: var(--divider);
    margin: 0 10px;
    vertical-align: -3px;
  }
</style>
</head>
<body>
  <div class="letterhead">
    <header class="brand">
      <span class="brand-dot"></span>
      <span class="brand-rule"></span>
      <h1 class="brand-name">Keystone Endodontics P.C.</h1>
      <p class="practitioner">Bertram L. Oswick, DDS</p>
    </header>

    <footer class="footer">
      <p class="address">2748 Tollard Avenue, Suite K, West Tollard, NY 14391</p>
      <svg class="footer-rule" width="614" height="8" viewBox="0 0 614 8" aria-hidden="true">
        <polygon points="0,2 614,2 580,4 580,7 34,7 34,4" fill="var(--brand-blue)"/>
      </svg>
      <p class="contacts">P: 716-392-5061<span class="sep"></span>F: 716-392-5087<span class="sep"></span>E: office@oswickroot.com</p>
    </footer>
  </div>
</body>
</html>
```